Website Re-design

Hi, I'm looking for help in redesigning my web site. I currently have a site www.brightferncove.example where I sell lamps, and while I like some aspects of the design, you can tell that I have done the graphics myself and am not a pro at it. I'd like help in redesigning it, and am open to completely new design graphics. I have made the 3 slider images myself, and I feel they could be a bit better, but I am not sure how to do it. For example, on the homepage, the 'About Us', 'Secured Shopping', and '$10 Off' graphics don't go well with the rest of the page. I would like more cohesion in the design and more visual interest in the header, which is pretty basic right now. Also, that the bottom footer is black, I would like instead something else. I am looking for just the layout of the homepage, and possibly once that is done to work on more visual interest in some of the informational pages and product pages. I am looking for just the design in the form of a photoshop file or files that I can incorporate into my site. Thank you!
Updates

Project Deadline Extended
Reason: I just made this project payment committed, so I'd like a chance for designers who only choose payment committed projects to submit artwork. Thank you.

This project is now payment guaranteed/ committed.  Thanks.

Industry/Entity Type

Shopping

```html
<!DOCTYPE html>
<html lang="en">
<head>
<meta charset="utf-8">
<title>Bright Fern Cove — Lamps & Lighting</title>
<link rel="stylesheet" href="https://fonts.googleapis.com/css2?family=Cabin:wght@400;500;600;700&family=Lobster+Two:ital,wght@0,400;0,700;1,400&family=Tinos&display=swap">
<style>
  :root{
    --navy:#0a1f5c;
    --blue:#1b5db8;
    --blue-bright:#2a7ad6;
    --ink:#3b3b3b;
    --ink-soft:#555;
    --line:#d8d8d8;
    --orange:#e8541a;
    --orange-dark:#c73f0c;
    --teal:#4bb4c8;
    --red:#e0262e;
    --green:#7ab567;
    --paper:#ffffff;
    --band:#dedede;
    --footer:#efefef;
    --wood:#cfd3d4;
  }
  *{box-sizing:border-box;margin:0;padding:0}
  html,body{width:1027px;height:1200px;overflow:hidden}
  body{position:relative;background:var(--paper);font-family:"Cabin",Arial,sans-serif;color:var(--ink)}

  /* Hero */
  .hero{position:absolute;left:0;top:0;width:1027px;height:532px;
    background:radial-gradient(ellipse 65% 75% at 55% 48%,var(--blue-bright) 0%,var(--blue) 45%,var(--navy) 100%)}
  .floor{position:absolute;left:0;top:532px;width:1027px;height:102px;
    background:linear-gradient(180deg,#eef0f0 0%,var(--wood) 30%,#b9bfc1 100%)}
  .lamp{position:absolute;left:596px;top:186px;width:246px;height:420px;
    background:linear-gradient(180deg,#f3f3f1 0%,#e6e6e3 38%,#37b6cf 40%,#2fa9c2 70%,#7fb25a 88%,#d9dde0 100%);
    border-radius:10px 10px 30px 30px}
  .headline{position:absolute;left:136px;top:160px;width:327px;text-align:center;color:#fff;
    font-family:"Lobster Two",cursive;text-shadow:0 2px 4px rgba(0,0,0,.35)}
  .headline .big{display:block;font-size:82px;line-height:90px}
  .headline .small{display:flex;align-items:center;gap:14px;font-size:42px;line-height:44px}
  .headline .small::before,.headline .small::after{content:"";flex:1;height:0;border-top:1px solid rgba(255,255,255,.45)}
  .product-name{position:absolute;left:120px;top:392px;width:360px;text-align:center;color:#fff;
    font-family:"Tinos",serif;font-size:24px;text-shadow:0 1px 3px rgba(0,0,0,.4)}
  .shop-button{position:absolute;left:191px;top:448px;width:217px;height:45px;border-radius:4px;
    background:linear-gradient(180deg,#f46a2a,var(--orange-dark));color:#fff;
    font-family:"Tinos",serif;font-size:23px;line-height:45px;text-align:center;
    box-shadow:0 2px 4px rgba(0,0,0,.4)}
  .slider-dots{position:absolute;left:280px;top:537px;display:flex;gap:5px}
  .slider-dots span{width:10px;height:10px;border-radius:50%;background:#fff}
  .slider-dots span.active{background:#111}

  /* Header */
  .site-header{position:absolute;left:120px;top:17px;width:787px;height:129px;background:var(--paper);
    border-radius:4px;box-shadow:0 3px 8px rgba(0,0,0,.35)}
  .brand{position:absolute;left:16px;top:24px;display:flex;align-items:center;gap:10px;
    font-size:23px;font-weight:600;color:var(--ink)}
  .brand .mark{width:34px;height:34px;border-radius:50%;background:var(--ink)}
  .account-links{position:absolute;right:15px;top:13px;font-size:11px;color:#666}
  .account-links b{font-weight:600;color:#444}
  .account-links .or{color:#aaa;margin:0 5px}
  .account-links span+span{margin-left:10px}
  .cart{position:absolute;right:8px;top:50px;display:flex;align-items:center;gap:6px;font-size:13px;color:#555}
  .cart .count{width:31px;height:20px;border-radius:4px;background:#3a3a3a;color:#fff;font-size:12px;text-align:center;line-height:20px;margin-left:6px}
  .cart .checkout{margin-left:8px;width:80px;height:25px;border:1px solid #c6c6c6;border-radius:4px;
    background:linear-gradient(#fafafa,#e2e2e2);text-align:center;line-height:23px;font-size:13px;color:#333}
  .main-nav{position:absolute;left:0;bottom:0;width:787px;height:40px;border-top:1px solid #ddd;
    background:linear-gradient(#f7f7f7,#e1e1e1);border-radius:0 0 4px 4px;display:flex}
  .main-nav a{display:block;padding:0 15px;line-height:40px;font-size:15px;color:#555;text-decoration:none;border-right:1px solid #cfcfcf}
  .search{position:absolute;right:9px;top:7px;width:135px;height:23px;border-radius:12px;background:#fff;
    box-shadow:inset 0 1px 2px rgba(0,0,0,.2);font-size:11px;color:#333;line-height:23px;padding-left:11px}
  .search svg{position:absolute;right:8px;top:4px}

  /* Features */
  .feature-band{position:absolute;left:0;top:634px;width:1027px;height:122px;
    background:linear-gradient(180deg,#ececec,var(--band))}
  .feature{position:absolute;top:691px;width:247px;height:230px;background:var(--paper);
    border:1px solid #e2e2e2;border-radius:4px;box-shadow:0 4px 6px rgba(0,0,0,.12);text-align:center}
  .feature .hex{position:absolute;left:94px;top:-34px}
  .feature h2{margin-top:34px;font-family:"Lobster Two",cursive;font-weight:400;font-style:italic;font-size:30px;line-height:36px}
  .feature .wave{display:block;margin:10px auto 0}
  .feature p{margin:14px auto 0;width:210px;font-size:13.5px;line-height:19px;color:var(--ink-soft)}
  .feature .more{position:absolute;left:50%;bottom:14px;transform:translateX(-50%);height:23px;padding:0 8px;
    border:1px solid #c8c8c8;border-radius:2px;background:linear-gradient(#f8f8f8,#dedede);font-size:11px;line-height:21px;color:#444}
  .about h2{color:var(--teal)} .secure h2{color:var(--red)} .offer h2{color:var(--green)}

  /* Footer */
  .site-footer{position:absolute;left:0;top:955px;width:1027px;height:245px;background:var(--footer)}
  .site-footer .scallop{position:absolute;left:0;top:-8px}
  .footer-col{position:absolute;top:42px;width:111px}
  .footer-col h3{font-size:13px;font-weight:500;color:#222;padding-bottom:6px;border-bottom:1px solid #ccc;margin-bottom:7px}
  .footer-col li{list-style:none;font-size:12px;line-height:20px;color:#555}
  .signup{position:absolute;left:692px;top:42px;width:215px}
  .signup h3{font-size:13px;font-weight:500;color:#222}
  .signup .field{margin-top:11px;display:flex;height:27px}
  .signup .field span{flex:1;border:1px solid #222;border-right:0;background:#fff;font-size:10px;line-height:25px;padding-left:6px;color:#333}
  .signup .field b{position:relative;width:64px;background:#111;color:#fff;font-size:12px;line-height:27px;padding-left:8px}
  .signup .field b::after{content:"";position:absolute;right:-10px;top:0;border-left:10px solid #111;border-top:13.5px solid transparent;border-bottom:13.5px solid transparent}
  .signup p{margin-top:8px;font-size:12px;color:#444}
  .social{display:flex;gap:8px;margin-top:14px}
  .social span{width:34px;height:34px;border-radius:50%;box-shadow:0 2px 3px rgba(0,0,0,.25)}
  .copyright{position:absolute;left:120px;top:200px;width:787px;border-top:1px solid #d2d2d2;padding-top:13px;text-align:center;font-size:12px;color:#444}
</style>
</head>
<body>

<section class="hero" role="img" aria-label="Deep blue faceted background behind the featured lamp"></section>
<div class="floor" role="img" aria-label="Whitewashed wooden floorboards"></div>
<div class="lamp" role="img" aria-label="Table lamp with white drum shade and teal-to-green glass base on a clear stand"></div>

<h1 class="headline">
  <span class="big">Light Up</span>
  <span class="small">the</span>
  <span class="big">Room</span>
</h1>
<p class="product-name">"The Lagoon" Medium Table Lamp</p>
<div class="shop-button">SHOP ALL LAMPS</div>
<div class="slider-dots"><span class="active"></span><span></span><span></span></div>

<header class="site-header">
  <div class="brand"><span class="mark"></span>Bright Fern Cove</div>
  <div class="account-links"><b>Sign in</b><span class="or">or</span>Create an account<span>My Account</span></div>
  <div class="cart">
    <svg width="24" height="18" viewBox="0 0 24 18" aria-hidden="true"><path d="M1 2h4l3 10h11l3-7H7" fill="none" stroke="#1e9bb4" stroke-width="2"/><circle cx="9" cy="15.5" r="1.8" fill="#1e9bb4"/><circle cx="18" cy="15.5" r="1.8" fill="#1e9bb4"/></svg>
    Shopping Cart<span class="count">0</span><span class="checkout">Checkout</span>
  </div>
  <nav class="main-nav">
    <a>HOME</a><a>SHOP</a><a>ABOUT US</a><a>CONTACT US</a>
    <div class="search">Search
      <svg width="16" height="16" viewBox="0 0 16 16" aria-hidden="true"><circle cx="6.5" cy="6.5" r="5" fill="none" stroke="#222" stroke-width="1.8"/><path d="M10 10l5 5" stroke="#222" stroke-width="2"/></svg>
    </div>
  </nav>
</header>

<div class="feature-band"></div>

<article class="feature about" style="left:120px">
  <svg class="hex" width="58" height="64" viewBox="0 0 58 64" aria-hidden="true"><path d="M29 1l27 15v32L29 63 2 48V16z" fill="var(--teal)"/><circle cx="29" cy="26" r="6" fill="#fff"/><path d="M18 42c0-7 5-10 11-10s11 3 11 10z" fill="#fff"/></svg>
  <h2>About Us</h2>
  <svg class="wave" width="214" height="6" viewBox="0 0 214 6" aria-hidden="true"><path d="M0 3q3-3 6 0t6 0 6 0 6 0 6 0 6 0 6 0 6 0 6 0 6 0 6 0 6 0 6 0 6 0 6 0 6 0 6 0 6 0 6 0 6 0 6 0 6 0 6 0 6 0 6 0 6 0 6 0 6 0 6 0 6 0 6 0 6 0 6 0 6 0 6 0 6 0" fill="none" stroke="#ccc" stroke-width="1.5"/></svg>
  <p>Bright Fern Cove provides beautiful and artistic home and hospitality lighting.</p>
  <span class="more">READ MORE</span>
</article>

<article class="feature secure" style="left:389px">
  <svg class="hex" width="58" height="64" viewBox="0 0 58 64" aria-hidden="true"><path d="M29 1l27 15v32L29 63 2 48V16z" fill="var(--red)"/><path d="M14 24h4l3 10h10" fill="none" stroke="#fff" stroke-width="2.2"/><path d="M19 27h14" stroke="#fff" stroke-width="2.2"/><circle cx="22" cy="38" r="1.8" fill="#fff"/><circle cx="29" cy="38" r="1.8" fill="#fff"/><rect x="34" y="30" width="10" height="9" rx="1" fill="#fff"/><path d="M36 30v-3a3 3 0 016 0v3" fill="none" stroke="#fff" stroke-width="1.8"/></svg>
  <h2>Secured Shopping</h2>
  <svg class="wave" width="214" height="6" viewBox="0 0 214 6" aria-hidden="true"><path d="M0 3q3-3 6 0t6 0 6 0 6 0 6 0 6 0 6 0 6 0 6 0 6 0 6 0 6 0 6 0 6 0 6 0 6 0 6 0 6 0 6 0 6 0 6 0 6 0 6 0 6 0 6 0 6 0 6 0 6 0 6 0 6 0 6 0 6 0 6 0 6 0 6 0 6 0" fill="none" stroke="#ccc" stroke-width="1.5"/></svg>
  <p>Shopping at Bright Fern Cove is secured and protected by industry standard best practices.</p>
  <span class="more">READ MORE</span>
</article>

<article class="feature offer" style="left:659px">
  <svg class="hex" width="58" height="64" viewBox="0 0 58 64" aria-hidden="true"><path d="M29 1l27 15v32L29 63 2 48V16z" fill="var(--green)"/><rect x="16" y="23" width="26" height="18" fill="#fff"/><path d="M16 23l13 10 13-10" fill="none" stroke="var(--green)" stroke-width="1.8"/></svg>
  <h2>$10 Off</h2>
  <svg class="wave" width="214" height="6" viewBox="0 0 214 6" aria-hidden="true"><path d="M0 3q3-3 6 0t6 0 6 0 6 0 6 0 6 0 6 0 6 0 6 0 6 0 6 0 6 0 6 0 6 0 6 0 6 0 6 0 6 0 6 0 6 0 6 0 6 0 6 0 6 0 6 0 6 0 6 0 6 0 6 0 6 0 6 0 6 0 6 0 6 0 6 0 6 0" fill="none" stroke="#ccc" stroke-width="1.5"/></svg>
  <p>$10 off any purchase when you sign up for our newsletter.</p>
  <span class="more">SIGN UP</span>
</article>

<footer class="site-footer">
  <svg class="scallop" width="1027" height="10" viewBox="0 0 1027 10" preserveAspectRatio="none" aria-hidden="true">
    <path d="M0 10 Q20 -2 40 10 T80 10 T120 10 T160 10 T200 10 T240 10 T280 10 T320 10 T360 10 T400 10 T440 10 T480 10 T520 10 T560 10 T600 10 T640 10 T680 10 T720 10 T760 10 T800 10 T840 10 T880 10 T920 10 T960 10 T1000 10 T1040 10 Z" fill="var(--footer)"/>
  </svg>
  <div class="footer-col" style="left:120px"><h3>HELP + INFO</h3><ul><li>Contact Us</li><li>Shipping Info</li><li>Returns</li><li>To The Trade</li><li>Privacy Policy</li><li>Terms of Use</li></ul></div>
  <div class="footer-col" style="left:254px"><h3>MY ACCOUNT</h3><ul><li>Sign In</li><li>Order Status</li><li>Order History</li><li>View Cart</li><li>Checkout</li></ul></div>
  <div class="footer-col" style="left:388px"><h3>ABOUT</h3><ul><li>Who We Are</li><li>Testimonials</li></ul></div>
  <div class="footer-col" style="left:522px;width:150px"><h3 style="width:111px">CONTACT</h3><ul><li>Contact Us</li><li>info@brightferncove.example</li></ul></div>
  <div class="signup">
    <h3>SIGN UP FOR BRIGHT FERN COVE EMAILS</h3>
    <div class="field"><span>Enter your email</span><b>JOIN US</b></div>
    <p>Because you love being the first to know</p>
    <div class="social"><span style="background:#3b6fc1"></span><span style="background:#37a9e0"></span><span style="background:#d22630"></span></div>
  </div>
  <div class="copyright">© 2013 Bright Fern Cove.&nbsp; All Rights Reserved</div>
</footer>

</body>
</html>
```